Animal Eye Clinic needs a Business card

We are a new veterinary ophthalmology practice (Ridgeline Pet Vision Care) and we need a business card designed. We only see animal eyes - we are not a regular veterinary clinic. We already have a logo. We are looking for a professional, good looking business card to hand out to our clients. We are looking for something simple but professional and contemporary. Our logo is likely the only picture/graphic that needs to be on the card.
Updates

Contact Information for Business Card

Delia Vossman, BSc, DVM, MSc, DipACVO
Veterinary Ophthalmologist

Phone: 250.418.3927
Email: ridgelinepetvisioncare@mailbox-example.net
Website: ridgelinepetvisioncare-example.net
Address: 1874 Thornbury Rd
Kelowna, BC, V1X 4M9

Colors

Designer to choose colors to be used in the design.

Requirements
Must have
• Our logo (attached)

```html
<!DOCTYPE html>
<html lang="en">
<head>
<meta charset="utf-8">
<title>Ridgeline Pet Vision Care – Business Card</title>
<link rel="stylesheet" href="https://fonts.googleapis.com/css2?family=Roboto:wght@300;400;500;700&display=swap">
<style>
  :root {
    --stage: #2b2b2c;
    --card: #1d1e20;
    --card-edge: #26272a;
    --teal: #14a2b2;
    --text: #e6e7e8;
    --muted: #b9bbbe;
    --rule: #8d8f93;
    --pattern-a: #232427;
    --pattern-b: #2c2d31;
  }
  * { box-sizing: border-box; margin: 0; padding: 0; }
  html, body { width: 1200px; height: 1108px; overflow: hidden; }
  body {
    background: var(--stage);
    font-family: "Roboto", Arial, sans-serif;
    display: flex;
    align-items: center;
    justify-content: center;
    gap: 60px;
  }
  .card {
    width: 420px;
    height: 700px;
    background: var(--card);
    border-radius: 28px;
    position: relative;
    overflow: hidden;
    box-shadow: 0 18px 40px rgba(0,0,0,.45);
  }

  /* Front */
  .card--front { color: var(--text); text-align: center; }
  .brand {
    position: absolute;
    top: 92px;
    left: 0; right: 0;
    display: flex;
    align-items: center;
    justify-content: center;
    gap: 14px;
  }
  .brand__dot {
    width: 46px; height: 46px;
    border-radius: 50%;
    background: var(--teal);
    flex: none;
  }
  .brand__name {
    color: var(--teal);
    font-weight: 700;
    font-size: 23px;
    line-height: 1.15;
    letter-spacing: .5px;
    text-transform: uppercase;
    text-align: left;
  }
  .person {
    position: absolute;
    top: 356px;
    left: 0; right: 0;
  }
  .person__name {
    color: var(--teal);
    font-weight: 700;
    font-size: 17px;
  }
  .person__title {
    font-weight: 400;
    font-size: 16px;
    margin-top: 4px;
  }
  .divider {
    display: flex;
    align-items: center;
    gap: 6px;
    margin: 18px auto 0;
    width: 250px;
  }
  .divider__line { flex: 1; height: 1px; background: var(--rule); }
  .icon {
    width: 24px; height: 24px;
    border-radius: 50%;
    background: var(--teal);
    display: flex; align-items: center; justify-content: center;
  }
  .icon svg { width: 14px; height: 14px; }
  .contact {
    margin-top: 14px;
    font-size: 15px;
    line-height: 1.45;
    font-weight: 400;
  }
  .contact__web span { color: var(--teal); }
  .rule {
    width: 250px; height: 1px;
    background: var(--rule);
    margin: 14px auto 0;
  }
  .address {
    margin-top: 16px;
    font-size: 17px;
    font-weight: 300;
    line-height: 1.4;
  }

  /* Back */
  .card--back { background: var(--card); }
  .back__texture {
    position: absolute;
    inset: 0;
    background:
      linear-gradient(200deg, var(--pattern-b) 0%, var(--pattern-a) 60%, var(--card) 85%);
  }
  .back__brand {
    position: absolute;
    right: 40px;
    bottom: 150px;
    display: flex;
    align-items: center;
    gap: 10px;
  }
  .back__brand .brand__dot { width: 34px; height: 34px; }
  .back__brand .brand__name { font-size: 15px; }
</style>
</head>
<body>

  <section class="card card--front" aria-label="Business card front">
    <div class="brand">
      <span class="brand__dot"></span>
      <span class="brand__name">Ridgeline Pet<br>Vision Care</span>
    </div>

    <div class="person">
      <p class="person__name">Delia Vossman, BSc, DVM, MSc, DipACVO</p>
      <p class="person__title">Veterinary Ophthalmologist</p>

      <div class="divider">
        <span class="divider__line"></span>
        <span class="icon" aria-label="Phone">
          <svg viewBox="0 0 24 24"><path fill="#1d1e20" d="M6.6 10.8a15.1 15.1 0 0 0 6.6 6.6l2.2-2.2c.3-.3.7-.4 1-.2 1.1.4 2.3.6 3.6.6.6 0 1 .4 1 1V20c0 .6-.4 1-1 1A17 17 0 0 1 3 4c0-.6.4-1 1-1h3.5c.6 0 1 .4 1 1 0 1.3.2 2.5.6 3.6.1.3 0 .7-.2 1z"/></svg>
        </span>
        <span class="icon" aria-label="Email">
          <svg viewBox="0 0 24 24"><path fill="#1d1e20" d="M3 5h18v14H3z"/><path fill="none" stroke="#14a2b2" stroke-width="1.8" d="M3.5 6l8.5 7 8.5-7"/></svg>
        </span>
        <span class="icon" aria-label="Website">
          <svg viewBox="0 0 24 24" fill="none" stroke="#1d1e20" stroke-width="2"><circle cx="12" cy="12" r="9"/><path d="M3 12h18M12 3c3 3 3 15 0 18M12 3c-3 3-3 15 0 18"/></svg>
        </span>
        <span class="divider__line"></span>
      </div>

      <div class="contact">
        <p>250.418.3927</p>
        <p>ridgelinepetvisioncare@mailbox-example.net</p>
        <p class="contact__web">www.<span>ridgelinepetvisioncare-example</span>.net</p>
      </div>

      <div class="rule"></div>

      <div class="address">
        <p>1874 Thornbury Rd</p>
        <p>Kelowna, BC, V1X 4M9</p>
      </div>
    </div>
  </section>

  <section class="card card--back" aria-label="Business card back">
    <div class="back__texture" role="img" aria-label="Tonal repeating brand pattern across the card back"></div>
    <div class="back__brand">
      <span class="brand__dot"></span>
      <span class="brand__name">Ridgeline Pet<br>Vision Care</span>
    </div>
  </section>

</body>
</html>
```